We need a .psd design for a store we are creating called Brisk Purses. I will need only the main home page designed.

The store will be an eCommerce website that sells custom printed men's wallets. Customers will come onto the website and be able to upload their own images or add text to the front, back and inside of the wallet. We will initially be launching with one wallet style and will be expanding our range in the future for now the only images of a wallet on the website should be of the style attached.

There will be multiple templates that a customer can choose and edit the design of so there will effectively be a large number of products on display in the store. However, on the homepage there should just be a couple of featured products and the main emphasis should be on the features of the wallet/website and links to other areas of the website (customise your own wallet, edit our templates, bespoke designer wallets).

For the styling of the website, it needs to be funky and fresh with lots of colour. The logo of the website is attached and the styling should mirror the logo style.

The main features of the website should be on the home page. These features are:
- 5 year money back guarantee on wallet
- High quality, durable leather, made to last
- customer can upload photo and edit them online with our online picture editor
- 3d mockup of the wallet as you are designing it to show what it looks like with custom images on
- Edit any of our ready made wallet designs

Features of this wallet may be used as well - these can be viewed on "Image 6" of the attached product image .psd files.

Attached are the logo for the website and the wallet product photos. The product photos are provided in .psd format and have smart objects so that you can add any image to the front/inside of the wallets for any images on the website you create. Fee free to edit them and use them for banner images and feature images however you feel necessary.

The term "what does you wallet say about you" should be used as this is a tagline for most of the marketing - based on the fact that the wallets are personalised to each individual they will show off that individuals personality and what they like.

The eventual website will be hosted on cartnest and will more than likely use the "TillBay" theme. This is a highly adaptable theme and examples of the layout styles for the homepage can be found here: http://harbor.quillpages.example/cartnest/tillbay-intro/?storefront=loom-assets however i do not want you to just copy a ready made template and stick some stock photos in - I only want one page designing here, put the effort in with the banners and feature images and you'll win this.

Any images that you create for hero sliders/banners should be provided in .psd format so that they can be edited as necessary in the future. A newsletter popup should also be designed as the website will have postwren integration, the newsletter popup is a 500 x 750 image that pops up with a message saying "subscribe to our newsletter and get 10% off your next order".

There should also be an area of the page that has customer testimonials.

Target Market(s)

Males, aged 18 - 45

Industry/Entity Type

Retail

Number of Pages Required

1 page

Font styles to use
Serif
Decorative
Script

Colors

Designer to choose colors to be used in the design.

Requirements
Must have
• Vibrant and uplifting feel to the website
• Design which reflects the logo
• Features of the website and wallets should feature prominently on the homepage (but not in banner/hero image)
Nice to have
• hipster/geek/easygoing vibe
• Images that have used the wallet .psd files and have different designs on them showing customers that anything can be printed on the wallets
• Custom images/styles for the featured images and main banner.
Should not have
• - Boring images
• - Stock Photos
• - Mundane feel
• - Square block style images - try putting images in circles or geometric shapes with colours, just adding a stock photo to some "lorem Ipsum" text will not win you this contest

```html
<!DOCTYPE html>
<html lang="en">
<head>
<meta charset="utf-8">
<title>Brisk Purses – Custom Printed Wallets</title>
<link rel="stylesheet" href="https://fonts.googleapis.com/css2?family=Montserrat:wght@500;700;800;900&family=Arimo:ital,wght@0,400;0,700;1,400&display=swap">
<style>
  :root {
    --ink: #1b1e24;
    --white: #ffffff;
    --page: #ffffff;
    --band: #f4f4f4;
    --card: #ececec;
    --red: #e2372f;
    --yellow: #f6e21a;
    --blue: #1a9ad6;
    --green: #0f8f43;
    --pink: #d83a8f;
    --leather: #3a3330;
    --leather-light: #6d5a4e;
    --dim: rgba(28, 30, 36, 0.42);
    --head: "Montserrat", Arial, sans-serif;
    --body: "Arimo", Arial, sans-serif;
  }
  * { box-sizing: border-box; margin: 0; padding: 0; }
  html, body { width: 1200px; height: 2324px; overflow: hidden; background: var(--page); }
  body { position: relative; font-family: var(--head); color: var(--ink); }

  .site-header { position: absolute; left: 0; top: 0; width: 1200px; height: 110px; }
  .brand { position: absolute; left: 107px; top: 36px; display: flex; align-items: center; gap: 12px; }
  .brand-mark { width: 38px; height: 38px; border-radius: 50%; background: var(--ink); }
  .brand-name { font-family: var(--head); font-weight: 800; font-size: 30px; color: var(--ink); letter-spacing: -0.5px; }
  .main-nav { position: absolute; right: 106px; top: 46px; display: flex; gap: 19px; }
  .main-nav a { font-weight: 700; font-size: 12px; color: var(--ink); text-decoration: none; letter-spacing: 0.2px; }
  .main-nav a.is-active { color: var(--red); }

  .hero { position: absolute; left: 0; top: 126px; width: 1200px; height: 500px; }
  .hero-band { position: absolute; left: 0; top: 0; }
  .hero-title { position: absolute; left: 0; width: 1200px; top: 4px; text-align: center; font-weight: 900; font-size: 40px; color: var(--ink); }
  .hero-photo { position: absolute; left: 136px; top: 146px; width: 130px; height: 200px; transform: rotate(-6deg);
    background: radial-gradient(circle at 60% 40%, #caa587 0 18%, transparent 40%),
                radial-gradient(circle at 30% 60%, #7b5a45 0 20%, transparent 42%),
                linear-gradient(160deg, #e8e2da, #b49f8e 60%, #6f5a4b);
    border: 8px solid var(--white); box-shadow: 0 4px 10px rgba(0,0,0,.25); }
  .hero-device { position: absolute; left: 900px; top: 76px; width: 134px; height: 296px; border-radius: 22px;
    border: 6px solid #d8d8d8;
    background: radial-gradient(circle at 30% 30%, var(--red) 0 14%, transparent 30%),
                radial-gradient(circle at 70% 60%, var(--green) 0 12%, transparent 28%),
                radial-gradient(circle at 40% 80%, var(--blue) 0 12%, transparent 28%),
                var(--yellow); }

  .quick-links { position: absolute; top: 628px; left: 137px; display: flex; gap: 40px; }
  .quick-link { width: 281px; height: 67px; color: var(--yellow); text-decoration: none;
    background: radial-gradient(circle at 92% 70%, var(--blue) 0 10%, transparent 22%), var(--ink);
    display: flex; flex-direction: column; justify-content: center; align-items: center; font-weight: 800; font-size: 19px; line-height: 1.1; }
  .quick-link:nth-child(2) { background: radial-gradient(circle at 90% 80%, var(--green) 0 9%, transparent 20%), var(--ink); }
  .quick-link:nth-child(3) { background: radial-gradient(circle at 88% 30%, var(--red) 0 14%, transparent 26%), var(--ink); }

  .features { position: absolute; top: 741px; left: 107px; width: 990px; height: 160px; }
  .feature { position: absolute; top: 0; font-size: 13.5px; line-height: 1.45; font-weight: 500; text-transform: uppercase; letter-spacing: -0.4px; }
  .feature svg { display: block; margin: 0 0 8px 14px; }
  .feature strong { font-weight: 800; }

  .section-title { position: absolute; left: 0; width: 1200px; text-align: center; font-weight: 800; font-size: 20px; }
  .featured-title { top: 950px; }
  .product-card { position: absolute; top: 1001px; width: 304px; height: 222px;
    background: radial-gradient(ellipse at 50% 55%, #f6f6f6 0 30%, var(--card) 70%); }

  .wallet-anatomy { position: absolute; left: 0; top: 1260px; width: 1200px; height: 400px; }

  .testimonials { position: absolute; left: 0; top: 1668px; width: 1200px; height: 489px; background: var(--band); }
  .swirl { position: absolute; border-radius: 48% 52% 44% 56%; }
  .swirl-left { left: -10px; top: 82px; width: 230px; height: 440px;
    background: radial-gradient(circle at 30% 20%, var(--yellow) 0 12%, transparent 24%),
                radial-gradient(circle at 70% 45%, var(--green) 0 12%, transparent 24%),
                radial-gradient(circle at 30% 65%, var(--red) 0 12%, transparent 24%),
                radial-gradient(circle at 65% 85%, var(--blue) 0 12%, transparent 24%),
                linear-gradient(170deg, var(--yellow), var(--blue) 50%, var(--red)); }
  .swirl-right { right: -10px; top: -68px; width: 240px; height: 420px;
    background: radial-gradient(circle at 30% 18%, var(--blue) 0 12%, transparent 24%),
                radial-gradient(circle at 65% 40%, var(--yellow) 0 12%, transparent 24%),
                radial-gradient(circle at 35% 62%, var(--green) 0 12%, transparent 24%),
                radial-gradient(circle at 70% 85%, var(--red) 0 12%, transparent 24%),
                linear-gradient(190deg, var(--red), var(--yellow) 50%, var(--blue)); }
  .testimonials-title { top: 40px; }
  .testimonial { position: absolute; left: 289px; width: 604px; }
  .testimonial h3 { font-family: var(--body); font-weight: 700; font-size: 16.5px; line-height: 19px; }
  .testimonial p { font-family: var(--body); font-style: italic; font-size: 16px; line-height: 19px; hyphens: manual; }
  .chevron { position: absolute; left: 588px; top: 448px; }

  .site-footer { position: absolute; left: 0; top: 2217px; width: 1200px; }
  .footer-nav { display: flex; justify-content: center; align-items: center; gap: 18px; }
  .footer-nav a { font-weight: 700; font-size: 11.5px; color: var(--ink); text-decoration: none; }
  .social { display: flex; gap: 19px; margin-left: 10px; }
  .social span { width: 14px; height: 14px; background: var(--ink); display: block; }
  .legal { margin-top: 28px; text-align: center; font-family: var(--body); font-size: 10px; }
  .legal a { color: var(--ink); }

  .overlay { position: absolute; inset: 0; background: var(--dim); }
  .newsletter { position: absolute; left: 225px; top: 153px; width: 751px; height: 500px;
    background: radial-gradient(circle at 15% 20%, var(--red) 0 8%, transparent 16%),
                radial-gradient(circle at 80% 75%, var(--green) 0 8%, transparent 16%),
                radial-gradient(circle at 25% 80%, var(--blue) 0 8%, transparent 16%),
                radial-gradient(circle at 85% 25%, var(--yellow) 0 8%, transparent 16%),
                linear-gradient(135deg, var(--yellow), var(--red) 25%, var(--blue) 45%, var(--green) 62%, var(--yellow) 80%, var(--red)); }
  .newsletter-close { position: absolute; right: 0; top: 0; width: 49px; height: 49px; background: var(--ink); display: flex; align-items: center; justify-content: center; }
  .newsletter-copy { position: absolute; left: 0; top: 100px; width: 751px; text-align: center; font-weight: 800; font-size: 34px; line-height: 41px; letter-spacing: -0.3px; color: var(--white); }
  .newsletter-copy span { background: var(--ink); padding: 0 6px; box-decoration-break: clone; -webkit-box-decoration-break: clone; }
  .newsletter-copy em { font-style: normal; color: var(--yellow); }
  .newsletter-email { position: absolute; left: 232px; top: 296px; width: 281px; height: 45px; border: 2px solid var(--ink); background: var(--white); }
  .newsletter-submit { position: absolute; left: 232px; top: 353px; width: 281px; height: 46px; background: var(--ink); color: var(--yellow);
    border: 0; font-family: var(--head); font-weight: 800; font-size: 19px; }
</style>
</head>
<body>
  <header class="site-header">
    <div class="brand"><span class="brand-mark"></span><span class="brand-name">Brisk Purses</span></div>
    <nav class="main-nav">
      <a class="is-active" href="#">HOME</a><a href="#">ABOUT US</a><a href="#">BROWSE OUR DESIGNS</a><a href="#">SIGN IN</a><a href="#">CONTACT US</a>
    </nav>
  </header>

  <section class="hero">
    <svg class="hero-band" width="420" height="500" viewBox="0 0 420 500"><polygon points="0,30 400,60 360,220 150,190 138,470 0,430" fill="var(--green)"/></svg>
    <h1 class="hero-title">funk up</h1>
    <div class="hero-photo" role="img" aria-label="Instant photo of a customer with their printed wallet"></div>
    <div class="hero-device" role="img" aria-label="Phone showing a colourful paint-splash wallet design"></div>
  </section>

  <nav class="quick-links">
    <a class="quick-link" href="#"><span>CREATE</span><span>YOUR OWN WALLET</span></a>
    <a class="quick-link" href="#"><span>EDIT</span><span>OUR TEMPLATES</span></a>
    <a class="quick-link" href="#"><span>BESPOKE</span><span>DESIGNER WALLETS</span></a>
  </nav>

  <section class="features">
    <div class="feature" style="left:0">
      <svg width="96" height="92" viewBox="0 0 96 92"><circle cx="48" cy="46" r="44" fill="var(--green)"/><path d="M34 40v-10a14 14 0 0 1 28 0v10" fill="none" stroke="var(--ink)" stroke-width="5"/><rect x="28" y="40" width="40" height="32" fill="var(--ink)"/><text x="48" y="66" text-anchor="middle" font-family="Montserrat,sans-serif" font-weight="800" font-size="20" fill="var(--white)">5</text></svg>
      <strong>5 year money-<br>back</strong> guarantee<br>on wallet
    </div>
    <div class="feature" style="left:185px">
      <svg width="96" height="92" viewBox="0 0 96 92"><circle cx="48" cy="46" r="44" fill="var(--yellow)"/><circle cx="48" cy="46" r="26" fill="none" stroke="var(--ink)" stroke-width="5"/><path d="M37 46l8 8 14-16" fill="none" stroke="var(--ink)" stroke-width="5"/></svg>
      <strong>High quality,</strong><br>durable leather,<br>made to last
    </div>
    <div class="feature" style="left:371px">
      <svg width="96" height="92" viewBox="0 0 96 92"><circle cx="48" cy="46" r="44" fill="var(--blue)"/><rect x="26" y="30" width="44" height="32" fill="none" stroke="var(--ink)" stroke-width="4"/><path d="M36 46h22M50 38l8 8-8 8" fill="none" stroke="var(--ink)" stroke-width="4"/></svg>
      <strong>3D mockup</strong><br>of the wallet as<br>you are designing
    </div>
    <div class="feature" style="left:577px">
      <svg width="96" height="92" viewBox="0 0 96 92"><circle cx="48" cy="46" r="44" fill="var(--red)"/><rect x="22" y="30" width="36" height="30" fill="var(--ink)"/><path d="M56 40l22 14-10 2 6 12-5 2-6-12-7 7z" fill="var(--white)" stroke="var(--ink)" stroke-width="3"/></svg>
      <strong>Edit</strong> any of our<br>ready made<br>wallet designs
    </div>
    <div class="feature" style="left:757px">
      <svg width="120" height="92" viewBox="0 0 120 92"><circle cx="50" cy="46" r="44" fill="var(--pink)"/><rect x="46" y="14" width="64" height="44" fill="var(--white)" stroke="var(--ink)" stroke-width="4"/><rect x="22" y="40" width="38" height="34" fill="var(--white)" stroke="var(--ink)" stroke-width="4"/><path d="M32 70v-8h18v8" fill="none" stroke="var(--ink)" stroke-width="4"/></svg>
      <strong>Upload your photo</strong><br>and edit them online with<br>our online picture editor
    </div>
  </section>

  <h2 class="section-title featured-title">FEATURED PRODUCTS</h2>
  <div class="product-card" style="left:107px" role="img" aria-label="Featured printed wallet product"></div>
  <div class="product-card" style="left:449px" role="img" aria-label="Featured printed wallet product"></div>
  <div class="product-card" style="left:790px" role="img" aria-label="Featured printed wallet product"></div>

  <svg class="wallet-anatomy" width="1200" height="400" viewBox="0 1260 1200 400">
    <defs>
      <radialGradient id="leather" cx="40%" cy="35%" r="70%">
        <stop offset="0" stop-color="var(--leather-light)"/><stop offset="1" stop-color="var(--leather)"/>
      </radialGradient>
      <linearGradient id="print" x1="0" y1="0" x2="1" y2="1">
        <stop offset="0" stop-color="var(--yellow)"/><stop offset="0.3" stop-color="var(--green)"/>
        <stop offset="0.55" stop-color="var(--yellow)"/><stop offset="0.75" stop-color="var(--red)"/><stop offset="1" stop-color="var(--blue)"/>
      </linearGradient>
      <path id="arc1" d="M295 1344a46 46 0 0 1 92 0"/>
      <path id="arc2" d="M243 1456a46 46 0 0 1 92 0"/>
      <path id="arc3" d="M295 1572a46 46 0 0 1 92 0"/>
      <path id="arc4" d="M806 1344a46 46 0 0 1 92 0"/>
      <path id="arc5" d="M877 1454a46 46 0 0 1 92 0"/>
      <path id="arc6" d="M806 1569a46 46 0 0 1 92 0"/>
    </defs>
    <g fill="none" stroke="var(--ink)" stroke-width="2">
      <polyline points="401,1344 500,1344 540,1395"/>
      <polyline points="349,1456 530,1456"/>
      <polyline points="401,1572 500,1572 540,1520"/>
      <polyline points="792,1344 700,1344 664,1395"/>
      <polyline points="863,1454 672,1454"/>
      <polyline points="792,1569 700,1569 664,1520"/>
    </g>
    <g role="img" aria-label="Close-up photos of wallet details">
      <circle cx="341" cy="1344" r="60" fill="var(--blue)"/><circle cx="341" cy="1344" r="36" fill="url(#leather)"/>
      <circle cx="289" cy="1456" r="60" fill="var(--red)"/><circle cx="289" cy="1456" r="36" fill="url(#leather)"/>
      <circle cx="341" cy="1572" r="60" fill="var(--green)"/><circle cx="341" cy="1572" r="36" fill="url(#leather)"/>
      <circle cx="852" cy="1344" r="60" fill="var(--yellow)"/><circle cx="852" cy="1344" r="36" fill="url(#leather)"/>
      <circle cx="923" cy="1454" r="60" fill="var(--ink)"/><circle cx="923" cy="1454" r="36" fill="url(#leather)"/>
      <circle cx="852" cy="1569" r="60" fill="var(--pink)"/><circle cx="852" cy="1569" r="36" fill="url(#leather)"/>
    </g>
    <g font-family="Montserrat,sans-serif" font-weight="800" font-size="8.5" fill="var(--white)" text-anchor="middle">
      <text><textPath href="#arc1" startOffset="50%">REINFORCED CORNERS</textPath></text>
      <text><textPath href="#arc2" startOffset="50%">SLIM DESIGN SEMI-SOFT</textPath></text>
      <text><textPath href="#arc3" startOffset="50%">COIN COMPARTMENT</textPath></text>
      <text fill="var(--ink)"><textPath href="#arc4" startOffset="50%">DURABLE LUXURY LEATHER</textPath></text>
      <text><textPath href="#arc5" startOffset="50%">CREDIT CARD SLOTS</textPath></text>
      <text><textPath href="#arc6" startOffset="50%">TWO NOTE POCKETS</textPath></text>
    </g>
    <rect x="530" y="1392" width="140" height="134" rx="6" fill="url(#print)" transform="rotate(4 600 1459)" role="img" aria-label="Wallet printed with a paint-splash design"/>
  </svg>

  <section class="testimonials">
    <div class="swirl swirl-left" role="img" aria-label="Colourful swirl pattern decoration"></div>
    <div class="swirl swirl-right" role="img" aria-label="Colourful swirl pattern decoration"></div>
    <h2 class="section-title testimonials-title">WHAT THEY SAY ABOUT US</h2>
    <article class="testimonial" style="top:89px"><h3>Lorem Ipsum Dolor</h3><p>sit amet, consectetur adipiscing elit, sed do eiusmod tempor incididunt ut labore et dolore magna aliqua. Ut enim ad minim veniam, quis nostrud exercitation ulla-mco laboris nisi ut aliquip ex ea commodo consequat.</p></article>
    <article class="testimonial" style="top:211px"><h3>Lorem Ipsum Dolor</h3><p>sit amet, consectetur adipiscing elit, sed do eiusmod tempor incididunt ut labore et dolore magna aliqua. Ut enim ad minim veniam, quis nostrud exercitation ulla-mco laboris nisi ut aliquip ex ea commodo consequat.</p></article>
    <article class="testimonial" style="top:330px"><h3>Lorem Ipsum Dolor</h3><p>sit amet, consectetur adipiscing elit, sed do eiusmod tempor incididunt ut labore et dolore magna aliqua. Ut enim ad minim veniam, quis nostrud exercitation ulla-mco laboris nisi ut aliquip ex ea commodo consequat.</p></article>
    <svg class="chevron" width="24" height="14" viewBox="0 0 24 14"><path d="M1 1l11 11L23 1" fill="none" stroke="var(--ink)" stroke-width="2"/></svg>
  </section>

  <footer class="site-footer">
    <nav class="footer-nav">
      <a href="#">HOME</a><a href="#">ABOUT US</a><a href="#">BROWSE OUR DESIGNS</a><a href="#">SIGN IN</a><a href="#">CONTACT US</a>
      <span class="social"><span></span><span></span><span></span></span>
    </nav>
    <p class="legal"><a href="#">Terms of Use</a> &amp; <a href="#">Privacy Policy</a> &nbsp;© 2018 Brisk Purses • All rights reserved</p>
  </footer>

  <div class="overlay"></div>
  <aside class="newsletter" role="img" aria-label="Newsletter popup on a colourful swirl pattern background">
    <div class="newsletter-close"><svg width="20" height="20" viewBox="0 0 20 20"><path d="M1 1l18 18M19 1L1 19" stroke="var(--white)" stroke-width="2"/></svg></div>
    <p class="newsletter-copy"><span>SUBSCRIBE TO<br>OUR NEWSLETTER<br>AND GET <em>10% OFF</em><br>YOUR NEXT ORDER</span></p>
    <div class="newsletter-email"></div>
    <button class="newsletter-submit">SUBSCRIBE</button>
  </aside>
</body>
</html>
```